NEW Modern Sleek Business Card for VR Language Startup

Our startup is using VR to lead the next wave of world language education. We need a two-sided business card that introduces the larger organization (Brightloom Language Inc) and our contact info on one side and shows the product, Glimwoorld, on the other side.

Side 1 (contact info)= Brightloom Logo and Contact info (name, title, phone, email)

Side 2 (product)= Glimworld logo, text, and website
Text= Culturally Immersive Language Learning Games
Website= www.glimworld-play.com

Target Market(s)

Education, Technology

Contact Information for Business Card

Contact info will be updated upon approval of the design. For now, put this as a placeholder.

Perry Dunmore
Founder & CEO
pdunmore@quillpost-mail.net
(555)-014-2286

Font styles to use
Other font styles liked:
• Gibson and Century Gothic are the brand fonts

Requirements
Nice to have
• I would love to see cohesion between the design and colors of the two logos. I have attached a few business card designs that I like, so you can get a feel for my preferred style.

```html
<!DOCTYPE html>
<html lang="en">
<head>
<meta charset="utf-8">
<title>Brightloom Language – Business Card</title>
<link href="https://fonts.googleapis.com/css2?family=Montserrat:wght@600&family=Didact+Gothic&display=swap" rel="stylesheet">
<style>
  :root {
    --backdrop: #3b312d;
    --card: #ffffff;
    --ink: #1d1d1f;
    --warm-1: #f7a531;
    --warm-2: #f5334a;
    --warm-3: #a43fd8;
    --cool-1: #2f7df5;
    --cool-2: #27d3ec;
    --link: #1aa0e8;
    --name-purple: #7a4be0;
  }
  * { box-sizing: border-box; margin: 0; padding: 0; }
  html, body { width: 1200px; height: 844px; overflow: hidden; }
  body {
    background: var(--backdrop);
    font-family: "Didact Gothic", "Century Gothic", sans-serif;
    color: var(--ink);
    position: relative;
  }
  .card {
    position: absolute;
    top: 268px;
    width: 540px;
    height: 308px;
    background: var(--card);
    overflow: hidden;
    box-shadow: 0 10px 30px rgba(0,0,0,.45);
  }
  .card--contact { left: 40px; }
  .card--product { left: 620px; }

  .edge-art { position: absolute; }
  .edge-art--warm-left {
    left: 0; top: 96px; width: 110px; height: 120px;
    background: linear-gradient(160deg, var(--warm-2), var(--warm-1));
    clip-path: polygon(0 8%, 100% 0, 70% 100%, 0 100%);
  }
  .edge-art--warm-right {
    right: 0; top: 0; width: 200px; height: 308px;
    background: linear-gradient(170deg, var(--warm-1), var(--warm-2) 55%, var(--warm-3));
    clip-path: polygon(30% 0, 100% 0, 100% 100%, 60% 100%, 0 70%, 25% 45%, 0 30%);
  }
  .edge-art--cool-left {
    left: 0; top: 0; width: 200px; height: 230px;
    background: linear-gradient(135deg, var(--cool-1), var(--cool-2));
    clip-path: polygon(0 0, 60% 0, 100% 35%, 55% 60%, 70% 100%, 0 100%);
  }
  .edge-art--cool-right {
    right: 0; top: 20px; width: 110px; height: 150px;
    background: linear-gradient(135deg, var(--cool-2), var(--cool-1));
    clip-path: polygon(40% 0, 100% 0, 100% 100%, 30% 80%, 0 40%);
  }

  .brand {
    position: absolute;
    display: flex; flex-direction: column; align-items: center; gap: 8px;
    font-family: "Montserrat", "Century Gothic", sans-serif;
    font-weight: 600;
  }
  .brand__dot { width: 46px; height: 46px; border-radius: 50%; }
  .brand--company { left: 170px; top: 70px; width: 200px; }
  .brand--company .brand__dot { background: var(--warm-2); }
  .brand--company .brand__name { font-size: 30px; letter-spacing: 2px; color: var(--ink); }
  .brand--product { left: 170px; top: 50px; width: 200px; }
  .brand--product .brand__dot { background: var(--cool-1); }
  .brand--product .brand__name { font-size: 32px; color: var(--ink); }

  .contact { position: absolute; left: 36px; top: 206px; }
  .contact__name {
    font-size: 19px; letter-spacing: .5px; text-transform: uppercase;
    background: linear-gradient(90deg, var(--warm-1), var(--warm-2), var(--name-purple));
    -webkit-background-clip: text; background-clip: text; color: transparent;
  }
  .contact__title { font-size: 14px; margin-bottom: 10px; }
  .contact__line { display: flex; align-items: center; gap: 6px; font-size: 14px; line-height: 1.4; }
  .contact__line svg { width: 14px; height: 14px; flex: none; }

  .product-info { position: absolute; left: 120px; width: 300px; top: 176px; text-align: center; }
  .product-info__tagline { font-size: 14px; letter-spacing: .8px; text-transform: uppercase; line-height: 1.3; }
  .product-info__url { margin-top: 6px; font-size: 15px; color: var(--link); }
</style>
</head>
<body>
  <section class="card card--contact" aria-label="Business card, contact side">
    <div class="edge-art edge-art--warm-left" role="img" aria-label="Warm orange-red gradient circuit decoration"></div>
    <div class="edge-art edge-art--warm-right" role="img" aria-label="Warm orange-to-purple gradient circuit decoration"></div>
    <div class="brand brand--company">
      <span class="brand__dot"></span>
      <span class="brand__name">Brightloom</span>
    </div>
    <div class="contact">
      <p class="contact__name">Perry Dunmore</p>
      <p class="contact__title">Founder &amp; CEO</p>
      <p class="contact__line">
        <svg viewBox="0 0 16 16" aria-hidden="true"><path fill="#f5334a" d="M3 1l3 3-1.5 2a9 9 0 0 0 5.5 5.5L12 10l3 3-2 2C6 15 1 10 1 3z"/></svg>
        (555)-014-2286
      </p>
      <p class="contact__line">
        <svg viewBox="0 0 16 16" aria-hidden="true"><rect x="1" y="3" width="14" height="10" fill="#f7a531"/><path d="M1 3l7 6 7-6" fill="none" stroke="#fff" stroke-width="1.4"/></svg>
        pdunmore@quillpost-mail.net
      </p>
    </div>
  </section>

  <section class="card card--product" aria-label="Business card, product side">
    <div class="edge-art edge-art--cool-left" role="img" aria-label="Blue-cyan gradient circuit decoration"></div>
    <div class="edge-art edge-art--cool-right" role="img" aria-label="Cyan gradient circuit decoration"></div>
    <div class="brand brand--product">
      <span class="brand__dot"></span>
      <span class="brand__name">Glimworld</span>
    </div>
    <div class="product-info">
      <p class="product-info__tagline">Culturally Immersive<br>Language Learning Games</p>
      <p class="product-info__url">www.glimworld-play.com</p>
    </div>
  </section>
</body>
</html>
```